Security Stickers (6)

I have 6 security stickers I need designed in vector digital ready to print files. I have done some layouts and ideas of what they should look like and size. If you have design thoughts and changes please make suggestions. Sizes that are better for printing etc.

Target Market(s)

Alarm customers, equipment

Industry/Entity Type

Security

Requirements
Must have
• Cohesive design with company
Nice to have
• Standout design
Should not have
• Respectful these will be on equipment and peoples houses

```html
<!DOCTYPE html>
<html lang="en">
<head>
<meta charset="utf-8">
<title>KVR Fire &amp; Security Systems – Stickers</title>
<link rel="stylesheet" href="https://fonts.googleapis.com/css2?family=Arimo:wght@400;700&family=Roboto+Condensed:wght@700&display=swap">
<style>
  :root {
    --red: #e8212b;
    --ink: #111111;
    --sky: #d3ebf7;
    --sky-light: #eef8fd;
    --globe: #a9d6f1;
    --navy: #2b3190;
    --white: #ffffff;
    --shadow: rgba(0, 0, 0, 0.35);
  }
  * { margin: 0; padding: 0; box-sizing: border-box; }
  html, body { width: 800px; height: 1200px; overflow: hidden; background: var(--white); }
  body { position: relative; font-family: "Arimo", Arial, sans-serif; color: var(--ink); }

  .sticker { position: absolute; overflow: hidden; box-shadow: 14px 16px 18px var(--shadow); }
  .abs { position: absolute; }
  .center { left: 0; right: 0; text-align: center; }

  .globe-art {
    position: absolute; border-radius: 50%;
    background: radial-gradient(circle at 45% 40%, var(--sky-light) 0%, var(--globe) 70%, rgba(169,214,241,0.3) 100%);
    opacity: 0.8;
  }

  .brand-mark { font-weight: 700; color: var(--red); letter-spacing: 6px; line-height: 1; }
  .brand-line { font-family: "Roboto Condensed", "Arial Narrow", sans-serif; font-weight: 700; color: var(--red); line-height: 1; letter-spacing: 0.5px; }
  .address { font-weight: 700; }
  .rule { position: absolute; height: 2px; background: var(--red); }
  .phone { font-weight: 700; color: var(--red); line-height: 1; }
  .license { font-weight: 700; font-size: 13px; }

  /* Sticker 1: emergency service label */
  .sticker-emergency { left: 31px; top: 24px; width: 652px; height: 322px;
    background: linear-gradient(135deg, var(--sky) 0%, var(--sky-light) 60%, var(--sky) 100%); }
  .sticker-emergency .phone-band { position: absolute; left: 0; right: 0; bottom: 0; height: 58px; background: var(--red); }

  /* Sticker 2: service label */
  .sticker-service { left: 31px; top: 378px; width: 652px; height: 290px; background: var(--white); }
  .sticker-service .service-band { position: absolute; left: 0; right: 0; top: 0; height: 80px; background: var(--red);
    color: var(--white); font-weight: 700; font-size: 46px; text-align: center; line-height: 80px; letter-spacing: 1px; word-spacing: 8px; }

  /* Sticker 3: monitoring label */
  .sticker-monitoring { left: 24px; top: 702px; width: 718px; height: 443px; background: var(--white);
    border: 1.5px solid var(--ink); border-radius: 26px; }
  .monitoring-frame { position: absolute; left: 8px; top: 7px; right: 8px; bottom: 7px; border: 8px solid var(--navy); border-radius: 22px;
    overflow: hidden; background: linear-gradient(135deg, var(--sky) 0%, var(--sky-light) 55%, var(--sky) 100%); }
  .fill-line { position: absolute; height: 1.5px; background: var(--ink); }
  .field-label { font-size: 21px; }
</style>
</head>
<body>

<section class="sticker sticker-emergency">
  <div class="globe-art" style="left:170px; top:-50px; width:440px; height:440px;" role="img" aria-label="Light blue globe with grid lines as background decoration"></div>
  <p class="abs license" style="left:12px; top:11px;">Ma. License 0147</p>
  <p class="abs center brand-mark" style="top:40px; font-size:88px;">KVR</p>
  <p class="abs center brand-line" style="top:138px; font-size:40px;">FIRE &amp; SECURITY SYSTEMS</p>
  <p class="abs center address" style="top:190px; font-size:22px;">PO Box 4178 Linwood Ma 01525</p>
  <div class="rule" style="left:9px; right:9px; top:221px;"></div>
  <p class="abs center address" style="top:232px; font-size:21px; letter-spacing:0.5px;">24 HOUR EMERGENCY SERVICE</p>
  <div class="phone-band"></div>
  <p class="abs center phone" style="top:268px; font-size:48px; color:var(--white);">1-800-555-0199</p>
</section>

<section class="sticker sticker-service">
  <div class="service-band">24 HOUR SERVICE</div>
  <p class="abs brand-mark" style="left:58px; top:96px; font-size:82px;">KVR</p>
  <p class="abs brand-line" style="left:24px; top:182px; font-size:32px;">FIRE &amp; SECURITY SYSTEMS</p>
  <div class="rule" style="left:24px; right:20px; top:226px;"></div>
  <p class="abs address" style="left:24px; top:251px; font-size:17px;">PO Box 4178 Linwood Ma 01525</p>
  <p class="abs phone" style="left:347px; top:243px; font-size:33px;">1-800-555-0199</p>
</section>

<section class="sticker sticker-monitoring">
  <div class="monitoring-frame">
    <div class="globe-art" style="left:168px; top:30px; width:370px; height:370px;" role="img" aria-label="Light blue globe with grid lines as background decoration"></div>
    <p class="abs center brand-mark" style="top:16px; font-size:70px;">KVR</p>
    <p class="abs center brand-line" style="top:92px; font-size:34px;">FIRE &amp; SECURITY SYSTEMS</p>
    <p class="abs center address" style="top:137px; font-size:21px;">PO Box 4178 Linwood Ma 01525</p>
    <div class="rule" style="left:22px; right:20px; top:167px;"></div>
    <p class="abs center address" style="top:183px; font-size:22px; letter-spacing:0.5px;">24 HOUR EMERGENCY SERVICE</p>
    <p class="abs center phone" style="top:212px; font-size:33px;">1-800-555-0199</p>
    <div class="rule" style="left:22px; right:20px; top:251px;"></div>
    <p class="abs center" style="top:266px; font-size:23px;">CENTRAL STATION MONITORING</p>
    <p class="abs field-label" style="left:24px; top:312px;">Phone #</p>
    <div class="fill-line" style="left:128px; right:20px; top:333px;"></div>
    <p class="abs field-label" style="left:41px; top:363px;">Acct. #</p>
    <div class="fill-line" style="left:131px; right:20px; top:384px;"></div>
    <p class="abs center license" style="top:391px; font-size:16px;">Ma. License 0147</p>
  </div>
</section>

</body>
</html>
```